Finiding oppertunites in Real Estate 6.15.20

size of ad 7” x 9.6”
1-I like the ad to stand out and attract people's attention.
2-you should be able to see the text of the ad clearly .. see the attachment anything in yellow is instructions.
3-the list of topics should not be the main part of the ad
4-if you decide you want a picture or vector of a person .. (you decide)
then it should be a white male about 25-30 years old wearing a solid white or blue shirt and not long hair.
5-leave 1 inch for footer
see attachment
Good luck

Target Market(s)

potential male students 25-35 years of age

Industry/Entity Type

Education

Requirements
Must have
• will stand out and people would want to see it.
should be able to read the words of ad
Nice to have
• how to make money in real estate on one line

```html
<!DOCTYPE html>
<html lang="en">
<head>
<meta charset="UTF-8">
<title>Real Estate Career Course – 12th Session</title>
<link href="https://fonts.googleapis.com/css2?family=Oswald:wght@500;600;700&family=Open+Sans:wght@400;600;700&display=swap" rel="stylesheet">
<style>
  :root {
    --navy: #12285a;
    --blue: #1f6fd1;
    --sky: #4fa3ef;
    --pale: #e6f1fc;
    --paper: #f6faff;
    --white: #ffffff;
  }
  * { margin: 0; padding: 0; box-sizing: border-box; }
  html, body { width: 876px; height: 1200px; overflow: hidden; }
  body { font-family: "Open Sans", Arial, sans-serif; color: var(--navy); background: var(--white); }

  .ad {
    position: relative;
    width: 876px;
    height: 1200px;
    overflow: hidden;
    background: linear-gradient(180deg, var(--paper) 0%, var(--white) 55%, var(--paper) 100%);
  }

  .corner-shape { position: absolute; top: 0; right: 0; }
  .dots { position: absolute; inset: 0; pointer-events: none; }

  .headline {
    position: absolute;
    left: 58px;
    top: 40px;
    font-family: "Oswald", Arial, sans-serif;
    font-weight: 700;
    font-size: 56px;
    line-height: 1;
    letter-spacing: 0.5px;
    color: var(--navy);
    text-transform: uppercase;
  }

  .intro-list {
    position: absolute;
    left: 58px;
    top: 176px;
    list-style: none;
  }
  .intro-list li {
    position: relative;
    padding-left: 34px;
    font-size: 21px;
    font-weight: 600;
    line-height: 1.3;
    margin-bottom: 12px;
    color: var(--navy);
  }
  .intro-list li::before,
  .topics li::before {
    content: "";
    position: absolute;
    left: 0;
    top: 6px;
    width: 16px;
    height: 16px;
    background: var(--blue);
    border-radius: 2px;
  }

  .hero-art {
    position: absolute;
    left: 140px;
    top: 300px;
    width: 640px;
    height: 340px;
    border-radius: 48% 52% 40% 60% / 55% 45% 55% 45%;
    background: radial-gradient(ellipse at 45% 55%, var(--white) 0%, var(--pale) 45%, var(--sky) 100%);
  }

  .remote-badge {
    position: absolute;
    left: 92px;
    top: 312px;
    width: 140px;
    height: 140px;
    border-radius: 50%;
    background: var(--white);
    box-shadow: 0 6px 18px rgba(18, 40, 90, 0.18);
    display: flex;
    align-items: center;
    justify-content: center;
    text-align: center;
    font-family: "Oswald", Arial, sans-serif;
    font-weight: 600;
    font-size: 24px;
    line-height: 1.1;
    color: var(--navy);
  }

  .session-title {
    position: absolute;
    left: 0;
    width: 100%;
    top: 648px;
    text-align: center;
    font-family: "Oswald", Arial, sans-serif;
    font-weight: 700;
    text-transform: uppercase;
    color: var(--navy);
    line-height: 1;
    white-space: nowrap;
  }
  .session-title .number { font-size: 112px; }
  .session-title .ordinal { font-size: 44px; vertical-align: 52px; margin-right: 6px; }
  .session-title .label { font-size: 86px; }

  .start-date {
    position: absolute;
    left: 0;
    width: 100%;
    top: 772px;
    text-align: center;
    font-family: "Oswald", Arial, sans-serif;
    font-weight: 600;
    font-size: 58px;
    line-height: 1;
    color: var(--navy);
    text-transform: uppercase;
    white-space: nowrap;
  }

  .topics-banner {
    position: absolute;
    left: 50%;
    top: 856px;
    transform: translateX(-50%);
    padding: 9px 46px;
    background: var(--blue);
    color: var(--white);
    font-weight: 700;
    font-size: 22px;
    letter-spacing: 0.5px;
    text-transform: uppercase;
    white-space: nowrap;
    clip-path: polygon(0 0, 100% 0, 95% 50%, 100% 100%, 0 100%, 5% 50%);
  }

  .topics {
    position: absolute;
    left: 60px;
    top: 918px;
    width: 760px;
    display: grid;
    grid-template-columns: 270px 270px 220px;
  }
  .topics ul { list-style: none; }
  .topics li {
    position: relative;
    padding-left: 30px;
    font-size: 20px;
    line-height: 1.3;
    margin-bottom: 10px;
    color: var(--navy);
    white-space: nowrap;
  }

  .footer {
    position: absolute;
    left: 0;
    bottom: 0;
    width: 100%;
    height: 84px;
    padding: 0 30px;
    border-top: 4px solid var(--blue);
    background: var(--white);
    display: flex;
    align-items: center;
    justify-content: center;
    font-weight: 600;
    font-size: 21px;
    color: var(--navy);
    white-space: nowrap;
  }
  .footer span { flex-shrink: 0; }
  .footer .divider { margin: 0 14px; color: var(--blue); }
</style>
</head>
<body>
  <main class="ad">
    <svg class="corner-shape" width="300" height="240" viewBox="0 0 300 240" aria-hidden="true">
      <path d="M90 0 H300 V240 C250 200 200 190 170 140 C140 90 120 40 90 0 Z" fill="#12285a"/>
      <path d="M150 0 H300 V150 C260 120 220 100 200 60 C185 30 170 10 150 0 Z" fill="#1f6fd1"/>
    </svg>

    <svg class="dots" width="876" height="1200" viewBox="0 0 876 1200" aria-hidden="true">
      <circle cx="690" cy="330" r="14" fill="#4fa3ef"/>
      <circle cx="760" cy="420" r="8" fill="#1f6fd1"/>
      <circle cx="120" cy="560" r="10" fill="#4fa3ef"/>
      <circle cx="800" cy="610" r="12" fill="#1f6fd1"/>
      <circle cx="60" cy="720" r="7" fill="#4fa3ef"/>
    </svg>

    <h1 class="headline">Real Estate<br>Career Course</h1>

    <ul class="intro-list">
      <li>How to Make Money In Real Estate?</li>
      <li>For those who have started or would like to go into Real Estate</li>
      <li>An investment in knowledge opens up untold opportunities</li>
    </ul>

    <div class="hero-art" role="img" aria-label="Illustration of a young man in a suit presenting a suburban house on a blue background"></div>

    <div class="remote-badge">Remote<br>Sessions</div>

    <h2 class="session-title">
      <span class="number">12</span><span class="ordinal">th</span><span class="label">Session Course</span>
    </h2>

    <p class="start-date">Classes Starting June 16</p>

    <div class="topics-banner">A Partial Listing of Topics</div>

    <section class="topics">
      <ul>
        <li>Single-family</li>
        <li>Multifamily</li>
        <li>Management</li>
        <li>Real Estate Concepts</li>
        <li>HUD properties</li>
      </ul>
      <ul>
        <li>Real Estate law</li>
        <li>Investment properties</li>
        <li>Foreclosures</li>
        <li>Rehab</li>
        <li>Due Diligence</li>
      </ul>
      <ul>
        <li>Foreclosures</li>
        <li>Short sales</li>
        <li>Development</li>
        <li>Finical modeling</li>
      </ul>
    </section>

    <footer class="footer">
      <span class="phone">0800 555 0142</span><span class="divider">|</span>
      <span class="web">propertypathacademy.info</span><span class="divider">|</span>
      <span class="web">propertypathacademy.com</span>
    </footer>
  </main>
</body>
</html>
```